KLV Plant Services

We are a heavy diesel mechanical business with additional air con certificates, remapping engine rebuilt

Contact Information for Business Card

Company Name, Director Name, Managing Director, Contact details, email and website

Font styles to use
Serif
Script

```html
<!DOCTYPE html>
<html lang="en">
<head>
<meta charset="utf-8">
<title>KLV Plant Services – Business Card</title>
<link rel="stylesheet" href="https://fonts.googleapis.com/css2?family=Exo+2:wght@700&family=Open+Sans:wght@400;600&display=swap">
<style>
  :root {
    --navy: #25226b;
    --black: #0b0b0c;
    --white: #ffffff;
    --backdrop: #3b3b3d;
    --grey-text: #4a4a4a;
    --card-shadow: rgba(0,0,0,.45);
  }
  * { box-sizing: border-box; margin: 0; padding: 0; }
  html, body { width: 1200px; height: 780px; overflow: hidden; }
  body {
    background: var(--backdrop);
    font-family: "Open Sans", sans-serif;
    display: flex;
    align-items: center;
    justify-content: center;
    gap: 60px;
  }
  .card {
    position: relative;
    width: 520px;
    height: 298px;
    background: var(--white);
    border-radius: 20px;
    overflow: hidden;
    box-shadow: 0 18px 40px var(--card-shadow);
  }
  .card__wave { position: absolute; inset: 0; width: 100%; height: 100%; }

  /* contact side */
  .identity {
    position: absolute;
    top: 20px;
    left: 30px;
    padding-left: 12px;
    border-left: 6px solid var(--navy);
  }
  .identity__name {
    font-family: "Exo 2", sans-serif;
    font-weight: 700;
    font-size: 17px;
    letter-spacing: .5px;
    color: var(--navy);
    line-height: 1.1;
  }
  .identity__role {
    font-size: 12px;
    color: var(--grey-text);
    margin-top: 2px;
  }
  .contact {
    position: absolute;
    left: 28px;
    top: 150px;
    color: var(--white);
    font-size: 12.5px;
    line-height: 1.45;
    list-style: none;
  }
  .contact__address { margin-bottom: 4px; padding-left: 19px; }
  .contact__item { display: flex; align-items: center; gap: 6px; }
  .contact__icon { width: 13px; height: 13px; flex: none; }

  .wordmark {
    position: absolute;
    display: flex;
    align-items: center;
    gap: 10px;
    font-family: "Exo 2", sans-serif;
    font-weight: 700;
    color: var(--navy);
    white-space: nowrap;
  }
  .wordmark__dot { border-radius: 50%; background: var(--navy); flex: none; }
  .wordmark--small { right: 36px; top: 112px; font-size: 26px; }
  .wordmark--small .wordmark__dot { width: 16px; height: 16px; }

  /* logo side */
  .card--front .wordmark--large {
    top: 50%; left: 50%;
    transform: translate(-50%, -50%);
    font-size: 38px;
  }
  .wordmark--large .wordmark__dot { width: 22px; height: 22px; }
</style>
</head>
<body>

  <article class="card card--back">
    <svg class="card__wave" viewBox="0 0 520 298" preserveAspectRatio="none" aria-hidden="true">
      <path d="M0 78 C160 72 205 170 300 228 C365 266 425 286 520 298 L0 298 Z" fill="var(--black)"/>
      <path d="M0 91 C160 86 200 176 292 233 C352 270 412 289 480 298 L0 298 Z" fill="var(--white)"/>
      <path d="M0 97 C160 91 200 180 290 236 C350 272 410 290 470 298 L0 298 Z" fill="var(--navy)"/>
    </svg>

    <header class="identity">
      <h1 class="identity__name">DANIEL REEVES</h1>
      <p class="identity__role">Managing Director</p>
    </header>

    <ul class="contact">
      <li class="contact__address">Your address, City<br>State, Zip 1234</li>
      <li class="contact__item">
        <svg class="contact__icon" viewBox="0 0 16 16" aria-hidden="true"><path d="M4 1l3 3-2 2c1 2 3 4 5 5l2-2 3 3-2 2C7 14 2 9 2 3z" fill="none" stroke="currentColor" stroke-width="1.4"/></svg>
        123 456 789
      </li>
      <li class="contact__item">
        <svg class="contact__icon" viewBox="0 0 16 16" aria-hidden="true"><rect x="4" y="1" width="8" height="14" rx="1.5" fill="none" stroke="currentColor" stroke-width="1.4"/><circle cx="8" cy="12.5" r=".9" fill="currentColor"/></svg>
        123 456 789
      </li>
      <li class="contact__item">
        <svg class="contact__icon" viewBox="0 0 16 16" aria-hidden="true"><rect x="1" y="3" width="14" height="10" rx="1" fill="none" stroke="currentColor" stroke-width="1.4"/><path d="M1 4l7 5 7-5" fill="none" stroke="currentColor" stroke-width="1.4"/></svg>
        info@klvplant.com
      </li>
      <li class="contact__item">
        <svg class="contact__icon" viewBox="0 0 16 16" aria-hidden="true"><circle cx="8" cy="8" r="6.5" fill="none" stroke="currentColor" stroke-width="1.4"/><path d="M1.5 8h13M8 1.5c-3 3.5-3 9.5 0 13M8 1.5c3 3.5 3 9.5 0 13" fill="none" stroke="currentColor" stroke-width="1.1"/></svg>
        www.klvplant.com
      </li>
    </ul>

    <div class="wordmark wordmark--small">
      <span class="wordmark__dot"></span>KLV Plant Services
    </div>
  </article>

  <article class="card card--front">
    <div class="wordmark wordmark--large">
      <span class="wordmark__dot"></span>KLV Plant Services
    </div>
  </article>

</body>
</html>
```